Birchwell Agency Condominium mail merge

We need a marketing proposal letter design to do a mail merge to potential e customers. We included our logo and an example of my miserable attempt to create a template. We are looking for a modern and attractive proposal template. Here is our website https://www.birchwellagency.example to be used for any additional information needed about us and our services.

Target Market(s)

New prospects

Industry/Entity Type

Insurance Agency

Requirements
Must have
• My project must have a modern professional look with merge fields similar to the file uploaded with this project.
Nice to have
• it would like have a condominium and a car icon graphic depicting there is additional discounts for both quotes bundled.
Should not have
• My project should not have any other logos or company name

```html
<!DOCTYPE html>
<html lang="en">
<head>
<meta charset="utf-8">
<title>Birchwell Agency – Condo Insurance Proposal</title>
<link rel="stylesheet" href="https://fonts.googleapis.com/css2?family=Montserrat:wght@500;700&family=Alegreya+Sans:wght@400;500;700&family=Tinos&family=PT+Serif:wght@400;700&family=Yesteryear&display=swap">
<style>
  :root {
    --green: #3db54a;
    --green-dark: #23902f;
    --orange: #f47f21;
    --ink: #3a3a3a;
    --muted: #6b6b6b;
    --row-alt: #e8e8e8;
    --alert: #c8102e;
    --sig: #1c1a4a;
  }
  * { margin: 0; padding: 0; box-sizing: border-box; }
  html, body { width: 848px; height: 1200px; overflow: hidden; background: #fff; }
  .letter { position: relative; width: 848px; height: 1200px; overflow: hidden; font-family: "Alegreya Sans", sans-serif; color: var(--ink); }
  .nowrap { white-space: nowrap; }

  .brand { position: absolute; left: 34px; top: 40px; display: flex; align-items: center; gap: 8px; }
  .brand-dot { width: 18px; height: 18px; border-radius: 50%; background: var(--orange); }
  .brand-name { font-family: "Alegreya Sans", sans-serif; font-weight: 700; font-size: 26px; color: var(--green); }

  .recipient { position: absolute; left: 38px; top: 124px; font-family: "Tinos", serif; font-size: 12px; line-height: 22.8px; color: #333; }
  .recipient .merge-lg { font-size: 16px; line-height: 20px; margin-bottom: 6px; }
  .recipient .merge-md { font-size: 13px; }

  .bundle-badge { position: absolute; left: 655px; top: 16px; width: 178px; height: 174px; border-radius: 14px; overflow: hidden; background: var(--orange); }
  .bundle-art { height: 106px; background: linear-gradient(135deg, #3db54a 0%, #4cc058 60%, #f3d94a 100%); }
  .bundle-text { text-align: center; color: #fff; font-family: "Montserrat", sans-serif; padding: 5px 4px 0; }
  .bundle-text .small { font-size: 7px; font-weight: 500; }
  .bundle-text .big { font-size: 11.5px; font-weight: 700; line-height: 14px; white-space: nowrap; }
  .bundle-text .big.url { font-size: 9.6px; }
  .bundle-text .mid { font-size: 11px; font-weight: 500; line-height: 13px; }

  .proposal-no { position: absolute; right: 25px; top: 210px; font-family: "Montserrat", sans-serif; font-weight: 700; font-size: 22px; color: var(--green); }
  .proposal-date { position: absolute; right: 21px; top: 239px; font-family: "Tinos", serif; font-size: 11.5px; color: #444; }

  .salutation { position: absolute; left: 38px; top: 334px; font-weight: 700; font-size: 14px; }
  .intro, .closing { position: absolute; left: 38px; width: 780px; font-size: 14.6px; line-height: 21.5px; text-align: justify; }
  .intro { top: 354px; }
  .closing { top: 779px; text-align: left; }

  .coverage { position: absolute; left: 35px; top: 453px; width: 779px; border: 1px solid #ccc; border-top: none; }
  .coverage-head { height: 35px; background: var(--orange); color: #fff; font-family: "Montserrat", sans-serif; font-weight: 500; font-size: 13.5px; display: flex; align-items: center; }
  .coverage-head span:first-child { margin-left: 27px; width: 272px; }
  .coverage-body { position: relative; }
  .coverage-row { height: 28.6px; display: flex; align-items: center; font-size: 12.6px; color: var(--muted); width: 492px; }
  .coverage-row:nth-child(even) { background: var(--row-alt); }
  .coverage-row span:first-child { margin-left: 23px; width: 278px; }
  .coverage-row.key span:first-child { color: #111; font-weight: 700; }
  .coverage-row.key span:last-child { font-weight: 500; }
  .premium-panel { position: absolute; left: 492px; top: 1px; width: 286px; height: 229px; background: var(--green); color: #fff; display: flex; align-items: center; justify-content: center; text-align: center; font-family: "PT Serif", serif; font-weight: 700; font-size: 16px; line-height: 20px; }

  .disclaimer { position: absolute; left: 47px; top: 724px; width: 760px; color: var(--alert); font-size: 12.6px; font-weight: 500; line-height: 21.5px; }

  .signoff { position: absolute; left: 34px; top: 915px; font-size: 14px; }
  .signature { position: absolute; left: 34px; top: 946px; font-family: "Yesteryear", cursive; font-size: 27px; color: var(--sig); }
  .sig-rule { position: absolute; left: 31px; top: 987px; width: 166px; height: 1px; background: #bbb; }
  .sig-title { position: absolute; left: 34px; top: 995px; font-family: "Montserrat", sans-serif; font-weight: 500; font-size: 12px; letter-spacing: 1.6px; color: #111; }

  .footer-shape { position: absolute; left: 0; top: 1070px; }
  .footer-info { position: absolute; right: 21px; top: 1140px; text-align: right; font-family: "PT Serif", serif; font-size: 14.5px; line-height: 22.5px; color: #fff; letter-spacing: 0.4px; }
</style>
</head>
<body>
<main class="letter">
  <header class="brand">
    <span class="brand-dot"></span>
    <span class="brand-name">Birchwell Agency</span>
  </header>

  <address class="recipient" style="font-style:normal">
    <div class="merge-lg">«encodedimbno»</div>
    <div>«first_name1» «last_name1»</div>
    <div>&lt;&lt;Address&gt;&gt;</div>
    <div>&lt;&lt;Address2&gt;&gt;</div>
    <div>&lt;&lt;City&gt;&gt;, &lt;&lt;State&gt;&gt;, &lt;&lt;Zip&gt;&gt;</div>
    <div class="merge-md">«presorttrayid»</div>
  </address>

  <aside class="bundle-badge">
    <div class="bundle-art" role="img" aria-label="Illustration of a condo house, a plus sign and a yellow car"></div>
    <div class="bundle-text">
      <div class="small">Switch your condo and car insurance to</div>
      <div class="big url">BIRCHWELLAGENCY.EXAMPLE</div>
      <div class="mid">to take advantage of</div>
      <div class="big">ADDITIONAL DISCOUNTS</div>
    </div>
  </aside>

  <div class="proposal-no">PROPOSAL NO</div>
  <div class="proposal-date">Date: &lt;&lt;DATE&gt;&gt;</div>

  <p class="salutation">Respected Sir,</p>
  <p class="intro">We have saved our clients $100s on their Condo Insurance. Call us at <span class="nowrap">407-555-0142</span> so we can do the same for you! Bundle your Condo and Auto insurance together for additional savings with a multi-policy discount. Below is a sample Condo Insurance policy purchased recently in Orlando from Birchwell Insurance Agency.</p>

  <section class="coverage">
    <div class="coverage-head"><span>COVERAGE</span><span>LIMIT</span></div>
    <div class="coverage-body">
      <div class="coverage-row"><span>Personal Property Protection</span><span>&lt;ColumnQ&gt;</span></div>
      <div class="coverage-row"><span>Increased Additional Living Expense</span><span>20%</span></div>
      <div class="coverage-row"><span>Loss Assessments</span><span>$2,000</span></div>
      <div class="coverage-row"><span>Family Liability Protection</span><span>$100,000</span></div>
      <div class="coverage-row"><span>Building Property Protection</span><span>&lt;ColumnK&gt;</span></div>
      <div class="coverage-row"><span>Building Codes Coverages</span><span>25%</span></div>
      <div class="coverage-row key"><span>All Perils Deductible</span><span>$500</span></div>
      <div class="coverage-row key"><span>Hurricane Deductible</span><span>$500</span></div>
      <div class="premium-panel">Total Annual Premium:<br>&lt;&lt;Yearly Premium&gt;&gt;</div>
    </div>
  </section>

  <p class="disclaimer">***The quoted premium is a sample premium based on a recent policy purchased in Orlando. Premium will differ based on information obtained on your application***</p>

  <p class="closing">If you are tired of paying too much for Condo Insurance and are wanting all of your insurance needs handled under one agency, then call us at <span class="nowrap">407-555-0142</span>. One call is all it takes to see if you’ve got the right coverage at the right price.</p>

  <p class="signoff">Sincerely,</p>
  <div class="signature">Marcus Halden</div>
  <div class="sig-rule"></div>
  <div class="sig-title">[ AGENCY PRINCIPAL ]</div>

  <svg class="footer-shape" width="848" height="130" viewBox="0 0 848 130" aria-hidden="true">
    <rect x="0" y="52" width="848" height="78" fill="var(--orange)"/>
    <polygon points="66,12 200,52 150,52" fill="var(--green-dark)"/>
    <polygon points="0,57 66,12 296,130 0,130" fill="var(--green)"/>
  </svg>
  <footer class="footer-info">
    <div>A: 2240 Lakeview Parkway Ste. 310 Oviedo, FL 32765</div>
    <div>P: 02 5550 4821 90 E: info@BirchwellAgency.example, W: BirchwellAgency.example</div>
  </footer>
</main>
</body>
</html>
```